Detail Shop Business card design

i need a business card design for my new detailing company called 'Brisk's Polish Works'. i want an all black and white design . simple, direct and to the point. i want the designer to choose a fitting font to match the logothe front should have logo, address, phone and email and the back side should have a slogan and text indicating that we offer services on anything including cars, trucks, motorcycles and RVs. slogan will read "we take pride in your ride"
maybe also very small on the back side the IG icon with Brisks_Polish_Works

phone 208.417.6352
address 3847 E Larkin Ave
Spokane WA 99214
email: BrisksPolish@mailvexo.com

Target Market(s)

all ages , auto enthusiasts

Industry/Entity Type

Automotive

Contact Information for Business Card

the front should have logo, address, phone and email and the back side should have a slogan and text indicating that we offer services on anything including cars, trucks, motorcycles and RVs. slogan will read "we take pride in your ride"

phone 208.417.6352
address 3847 E Larkin Ave
Spokane WA 99214

Colors
000000
ffffff

Requirements
Must have
• bold font and very simple design with good spacing
Nice to have
• anything creative from the designer indicating we service any types of vehicles
Should not have
• any colors ,

```html
<!DOCTYPE html>
<html lang="en">
<head>
<meta charset="utf-8">
<title>Brisk's Polish Works – Business Card</title>
<link rel="stylesheet" href="https://fonts.googleapis.com/css2?family=Lato:wght@300;400;700&family=Tinos&family=Oswald:wght@400&display=swap">
<style>
  :root {
    --backdrop: #353536;
    --card: #1d1d1e;
    --card-deco: #262627;
    --ink: #f2f2f2;
    --ink-soft: #d6d6d6;
    --rule: #4a4a4b;
  }
  * { box-sizing: border-box; margin: 0; padding: 0; }
  html, body {
    width: 1200px; height: 1108px; overflow: hidden;
    background: var(--backdrop);
  }
  .sheet {
    position: relative; width: 1200px; height: 1108px;
    display: flex; justify-content: center; align-items: center; gap: 60px;
  }
  .card {
    position: relative; width: 440px; height: 760px;
    background: var(--card); border-radius: 22px; overflow: hidden;
    color: var(--ink);
  }
  /* front */
  .brand {
    position: absolute; top: 90px; left: 0; right: 0;
    display: flex; flex-direction: column; align-items: center; gap: 22px;
  }
  .brand-dot {
    width: 90px; height: 90px; border-radius: 50%;
    border: 4px solid var(--ink);
  }
  .brand-name {
    font-family: "Lato", sans-serif; font-weight: 700;
    font-size: 40px; line-height: 1.15; text-align: center;
    color: var(--ink);
  }
  .contact {
    position: absolute; top: 450px; left: 50px; right: 50px;
    font-family: "Lato", sans-serif; font-weight: 400;
    font-size: 21px; line-height: 1.3; text-align: center; color: var(--ink-soft);
  }
  .contact-group { padding: 12px 0; }
  .contact-group + .contact-group { border-top: 1px solid var(--rule); }
  .handle { display: flex; flex-direction: column; align-items: center; gap: 6px; }
  .handle-dot { width: 22px; height: 22px; border-radius: 50%; background: var(--ink-soft); }
  .contact-end { border-top: 1px solid var(--rule); margin-top: 6px; }
  /* back */
  .deco {
    position: absolute; top: 0; left: 0; width: 100%; height: 420px;
    background: linear-gradient(160deg, var(--card-deco) 0%, var(--card) 85%);
  }
  .services {
    position: absolute; top: 255px; left: 30px; right: 30px;
    font-family: "Tinos", serif; font-size: 27px; line-height: 1.5;
    text-transform: uppercase; text-align: center; color: var(--ink);
  }
  .slogan {
    position: absolute; top: 480px; left: 56px; right: 30px;
    font-family: "Oswald", sans-serif; font-weight: 400;
    font-size: 66px; line-height: 1.2; color: var(--ink-soft);
  }
</style>
</head>
<body>
<main class="sheet">
  <section class="card card-front">
    <div class="brand">
      <div class="brand-dot"></div>
      <div class="brand-name">Brisk's<br>Polish Works</div>
    </div>
    <div class="contact">
      <div class="contact-group">
        208.417.6352<br>BrisksPolish@mailvexo.com
      </div>
      <div class="contact-group">
        3847 E Larkin Ave<br>Spokane WA 99214
      </div>
      <div class="contact-group handle">
        <span class="handle-dot"></span>
        <span>Brisks_Polish_Works</span>
      </div>
      <div class="contact-end"></div>
    </div>
  </section>

  <section class="card card-back">
    <div class="deco" role="img" aria-label="Faint backdrop decoration of the shop's vehicle emblem"></div>
    <p class="services">We offer services on<br>including cars, trucks<br>motorcycles and RVs.</p>
    <p class="slogan">We take pride<br>in your ride</p>
  </section>
</main>
</body>
</html>
```